Business Card for Industrial Distributor

We need a business card design for an industrial distributor. We sell machine parts for the manufacturing and oil industry. We would like the cards to look clean and modern but with a touch of industry.

Our colors are blue/white.

Please feel free to visit our website www.korvelpartsco.com

Target Market(s)

mexican manufacturers in the automobile/aerospace industry

Industry/Entity Type

Industrial

Colors
ffffff
0555a3

```html
<!DOCTYPE html>
<html lang="en">
<head>
<meta charset="utf-8">
<title>Korvel Business Card</title>
<link href="https://fonts.googleapis.com/css2?family=Roboto:wght@300;400;500;900&family=Roboto+Condensed:wght@400;700&display=swap" rel="stylesheet">
<style>
  :root {
    --brand-blue: #0555a3;
    --brand-blue-light: #1b74c4;
    --brand-blue-deep: #1d4aa8;
    --white: #ffffff;
    --ink: #1b1b1d;
    --band-dark: #252628;
    --panel-dark: #1c1c1e;
    --panel-dark-soft: #29292c;
    --muted: #c9cbcf;
    --grey-text: #8a8d92;
    --stage: #e9ebee;
  }
  * { margin: 0; padding: 0; box-sizing: border-box; }
  html, body { width: 1200px; height: 900px; overflow: hidden; }
  body {
    background: var(--stage);
    font-family: "Roboto", Arial, sans-serif;
    position: relative;
  }
  .card {
    position: absolute;
    left: 300px;
    width: 600px;
    height: 343px;
    border-radius: 22px;
    overflow: hidden;
    box-shadow: 0 10px 28px rgba(0,0,0,0.18);
  }
  .card--front { top: 70px; background: var(--white); }
  .card--back {
    top: 487px;
    background: radial-gradient(ellipse at 62% 40%, var(--brand-blue-light) 0%, var(--brand-blue-deep) 70%);
  }

  /* front */
  .front-lower {
    position: absolute;
    left: 0; right: 0; bottom: 0; height: 150px;
    border-top: 6px solid var(--brand-blue);
  }
  .front-lower__texture {
    position: absolute;
    inset: 0;
    background: linear-gradient(160deg, var(--panel-dark-soft) 0%, var(--panel-dark) 70%);
  }
  .wordmark {
    position: absolute;
    display: flex; align-items: center; gap: 10px;
    font-weight: 900;
    letter-spacing: -1px;
  }
  .wordmark__dot { border-radius: 50%; flex: none; }
  .front-mark { left: 36px; top: 40px; font-size: 58px; color: var(--brand-blue); }
  .front-mark .wordmark__dot { width: 40px; height: 40px; background: var(--brand-blue); }

  .person {
    position: absolute;
    right: 34px; top: 112px;
    padding-right: 14px;
    border-right: 5px solid var(--brand-blue);
    text-align: right;
    font-family: "Roboto Condensed", Arial, sans-serif;
  }
  .person__name { font-size: 27px; font-weight: 700; color: var(--ink); line-height: 1.05; }
  .person__name span { color: var(--brand-blue); }
  .person__role { font-size: 15px; color: var(--grey-text); letter-spacing: 0.5px; margin-top: 3px; }

  .contact {
    position: absolute;
    z-index: 1;
    font-family: "Roboto Condensed", Arial, sans-serif;
    font-size: 16px; line-height: 1.45;
    color: var(--muted);
  }
  .contact__label { color: var(--brand-blue-light); }
  .contact--left { left: 36px; top: 26px; }
  .contact--right { right: 40px; top: 26px; text-align: right; }

  /* back */
  .back-band {
    position: absolute;
    left: 0; right: 0; top: 96px; height: 150px;
    background: var(--band-dark);
  }
  .back-mark { left: 120px; top: 26px; font-size: 70px; color: var(--white); }
  .back-mark .wordmark__dot { width: 48px; height: 48px; background: var(--white); }
  .back-web {
    position: absolute;
    left: 300px; top: 112px;
    display: flex; align-items: center; gap: 6px;
    font-size: 15px; font-weight: 300; color: var(--white); letter-spacing: 0.5px;
  }
</style>
</head>
<body>

  <section class="card card--front" aria-label="Card front">
    <div class="wordmark front-mark"><span class="wordmark__dot"></span>Korvel</div>

    <div class="person">
      <div class="person__name"><span>DANIEL</span> REYES</div>
      <div class="person__role">MARKETING HEAD</div>
    </div>

    <div class="front-lower">
      <div class="front-lower__texture" role="img" aria-label="Dark carbon-fibre texture panel"></div>
      <div class="contact contact--left">
        <div><span class="contact__label">Tel.</span> (555) 014 - 2290</div>
        <div><span class="contact__label">Email.</span> sales@korvelpartsco.com</div>
        <div><span class="contact__label">Web.</span> korvelpartsco.com</div>
      </div>
      <div class="contact contact--right">
        <div><span class="contact__label">Fax.</span> (555) 014 - 2291</div>
        <div>1420 Harlow Mill Rd.</div>
        <div>Eastbrook, TX 70100</div>
      </div>
    </div>
  </section>

  <section class="card card--back" aria-label="Card back">
    <div class="back-band">
      <div class="wordmark back-mark"><span class="wordmark__dot"></span>Korvel</div>
      <div class="back-web">
        <svg width="13" height="13" viewBox="0 0 14 14" aria-hidden="true">
          <circle cx="7" cy="7" r="6" fill="none" stroke="#ffffff" stroke-width="1.2"/>
          <ellipse cx="7" cy="7" rx="2.6" ry="6" fill="none" stroke="#ffffff" stroke-width="1"/>
          <line x1="1" y1="7" x2="13" y2="7" stroke="#ffffff" stroke-width="1"/>
        </svg>
        www.korvelpartsco.com
      </div>
    </div>
  </section>

</body>
</html>
```